Falbrook Company Notepad / Grid pad / Graph pad

I need a "modern" version of this graph pad. The information at the top needs to be shown, along with the graph lines, however, I need this more "interesting" than it currently is. This will be printed and bound at the TOP edge with 50 sheets per pack.

Target Market(s)

Clients - Want to show sophistication and not childish.

Industry/Entity Type

Structural Engineering

Font styles to use
Sans Serif

Colors
0255a3
85abd2

Requirements
Must have
• My project must have all of the elements currently shown on the pdf
Should not have
• My project should not have clipart images.

Files

```html
<!DOCTYPE html>
<html lang="en">
<head>
<meta charset="utf-8">
<title>Falbrook Company Graph Pad</title>
<link href="https://fonts.googleapis.com/css2?family=Source+Sans+3:wght@400;600;700&display=swap" rel="stylesheet">
<style>
  :root {
    --navy: #1e5275;
    --paper: #f5f4f2;
    --swoosh: #7b8288;
    --green: #00a651;
    --grid-line: #bdbdbd;
    --grid-frame: #777777;
    --field-border: #8a8a8a;
    --ink: #111111;
    --muted: #6f7a80;
  }
  * { margin: 0; padding: 0; box-sizing: border-box; }
  html, body { width: 956px; height: 1200px; overflow: hidden; background: var(--paper); }
  body { font-family: "Source Sans 3", sans-serif; }
  .sheet { position: relative; width: 956px; height: 1200px; background: var(--paper); }
  .header-band { position: absolute; left: 0; top: 0; width: 956px; height: 140px; }
  .brand { position: absolute; left: 62px; top: 82px; }
  .brand-name { font-size: 31px; font-weight: 700; color: var(--navy); letter-spacing: 0.5px; line-height: 1; }
  .brand-tagline { margin-top: 8px; font-size: 9.5px; font-weight: 600; color: var(--muted); }
  .field-label { position: absolute; font-size: 14.5px; font-weight: 600; color: var(--navy); text-align: right; width: 90px; }
  .field-box { position: absolute; height: 24px; border: 1px solid var(--field-border); background: var(--paper); }
  .field-of { position: absolute; font-size: 14.5px; font-weight: 600; color: var(--ink); }
  .graph-area {
    position: absolute; left: 69px; top: 215px; width: 826px; height: 871px;
    border: 1.5px solid var(--grid-frame);
    background-image:
      linear-gradient(to right, var(--grid-line) 1px, transparent 1px),
      linear-gradient(to bottom, var(--grid-line) 1px, transparent 1px);
    background-size: 25.8px 18.93px;
    background-position: -1px -1px;
  }
  .contact-line {
    position: absolute; left: 0; width: 956px; top: 1126px;
    display: flex; justify-content: center; align-items: center; gap: 6px;
    font-size: 14.5px; color: var(--ink);
  }
  .contact-line svg { width: 13px; height: 13px; fill: var(--navy); }
  .contact-gap { width: 10px; }
  .base-stripe { position: absolute; left: 0; bottom: 0; width: 956px; height: 11px; background: var(--green); }
</style>
</head>
<body>
<div class="sheet">
  <svg class="header-band" viewBox="0 0 956 140" aria-hidden="true">
    <path d="M0 140 C 30 45 260 20 470 20 C 700 20 880 34 956 49 V0 H0 Z" fill="var(--navy)"/>
    <path d="M0 150 C 32 52 262 27 470 27 C 700 27 880 41 956 55" fill="none" stroke="var(--swoosh)" stroke-width="6"/>
  </svg>

  <div class="brand">
    <div class="brand-name">Falbrook Company</div>
    <div class="brand-tagline">Structure | Precision | Service</div>
  </div>

  <div class="field-label" style="left:356px;top:63px;">Project</div>
  <div class="field-box" style="left:457px;top:61px;width:173px;"></div>
  <div class="field-label" style="left:356px;top:92px;">Task</div>
  <div class="field-box" style="left:457px;top:90px;width:173px;"></div>
  <div class="field-label" style="left:356px;top:124px;">Page</div>
  <div class="field-box" style="left:457px;top:123px;width:61px;"></div>
  <div class="field-of" style="left:534px;top:125px;">of</div>
  <div class="field-box" style="left:569px;top:123px;width:61px;"></div>

  <div class="field-label" style="left:604px;top:63px;">Job No</div>
  <div class="field-box" style="left:705px;top:61px;width:172px;"></div>
  <div class="field-label" style="left:604px;top:92px;">Author</div>
  <div class="field-box" style="left:705px;top:90px;width:172px;"></div>
  <div class="field-label" style="left:604px;top:124px;">Date</div>
  <div class="field-box" style="left:705px;top:123px;width:172px;"></div>

  <div class="graph-area"></div>

  <div class="contact-line">
    <svg viewBox="0 0 24 24" aria-hidden="true"><path d="M12 1a8 8 0 0 0-8 8c0 6 8 14 8 14s8-8 8-14a8 8 0 0 0-8-8zm0 11a3 3 0 1 1 0-6 3 3 0 0 1 0 6z"/></svg>
    <span>215 Harbor Lane, Suite 302, Port Ellis, FL 33990</span>
    <span class="contact-gap"></span>
    <svg viewBox="0 0 24 24" aria-hidden="true"><path d="M6.6 10.8a15 15 0 0 0 6.6 6.6l2.2-2.2a1 1 0 0 1 1-.25 11.4 11.4 0 0 0 3.6.57 1 1 0 0 1 1 1V20a1 1 0 0 1-1 1A17 17 0 0 1 3 4a1 1 0 0 1 1-1h3.5a1 1 0 0 1 1 1c0 1.25.2 2.45.57 3.570a1 1 0 0 1-.25 1z"/></svg>
    <span>555.014.2290</span>
    <span class="contact-gap"></span>
    <svg viewBox="0 0 24 24" aria-hidden="true"><path d="M12 2a10 10 0 1 0 0 20 10 10 0 0 0 0-20zm6.9 6h-3a15.7 15.7 0 0 0-1.4-3.6A8 8 0 0 1 18.9 8zM12 4a14 14 0 0 1 1.9 4h-3.8A14 14 0 0 1 12 4zM4.3 14a8 8 0 0 1 0-4h3.4a16.5 16.5 0 0 0 0 4zm.8 2h3a15.7 15.7 0 0 0 1.4 3.6A8 8 0 0 1 5.1 16zm3-8h-3a8 8 0 0 1 4.4-3.6A15.7 15.7 0 0 0 8.1 8zM12 20a14 14 0 0 1-1.9-4h3.8A14 14 0 0 1 12 20zm2.3-6H9.7a14.7 14.7 0 0 1 0-4h4.6a14.7 14.7 0 0 1 0 4zm.2 5.6a15.7 15.7 0 0 0 1.4-3.6h3a8 8 0 0 1-4.4 3.6zm1.8-5.6a16.5 16.5 0 0 0 0-4h3.4a8 8 0 0 1 0 4z"/></svg>
    <span>www.falbrookcompany.com</span>
  </div>

  <div class="base-stripe"></div>
</div>
</body>
</html>
```